Brindovalle Business cards

Dear team, I need to get the design file to suit it to our team. The focus of the business card is the Automotive Market and the design must be in black colour and the logo must be in glossy black. On the front of the card I need to get the following info:

- Name and Surname
- Title
- eMail
- Phone Number
- Skype account
- domain address

```html
<!DOCTYPE html>
<html lang="en">
<head>
<meta charset="utf-8">
<title>Brindovalle Business Cards</title>
<link rel="stylesheet" href="https://fonts.googleapis.com/css2?family=Oswald:wght@600&family=Source+Sans+3:wght@400;700&display=swap">
<style>
  :root {
    --stage-light: #4a4a4a;
    --stage-dark: #1f1f1f;
    --card: #1b1b1c;
    --card-edge: #111112;
    --red: #e3222b;
    --white: #f4f4f4;
    --muted: #cfcfcf;
  }
  * { margin: 0; padding: 0; box-sizing: border-box; }
  html, body { width: 1200px; height: 900px; overflow: hidden; }
  body {
    background: radial-gradient(ellipse at 55% 55%, var(--stage-light), var(--stage-dark) 75%);
    font-family: "Source Sans 3", Arial, sans-serif;
    display: flex;
    align-items: center;
    justify-content: center;
    gap: 40px;
  }
  .card {
    width: 540px;
    height: 309px;
    background: var(--card);
    border-radius: 26px;
    box-shadow: 0 4px 0 var(--card-edge), 0 20px 40px rgba(0,0,0,.45);
    position: relative;
    overflow: hidden;
  }
  /* front: brand side */
  .card--brand {
    display: flex;
    align-items: center;
    justify-content: center;
    gap: 14px;
  }
  .brand-dot {
    width: 30px; height: 30px;
    border-radius: 50%;
    background: var(--red);
  }
  .brand-name {
    color: var(--white);
    font-weight: 700;
    font-size: 50px;
    letter-spacing: -0.5px;
  }
  /* back: contact side */
  .card--contact { padding: 0 40px; }
  .contact-top {
    position: absolute;
    top: 92px; left: 40px; right: 40px;
    display: flex;
    align-items: center;
    justify-content: center;
    gap: 22px;
  }
  .person { text-align: right; }
  .person-name {
    font-family: "Oswald", "Arial Narrow", sans-serif;
    font-weight: 600;
    color: var(--red);
    font-size: 32px;
    text-transform: uppercase;
    line-height: 1;
    letter-spacing: .5px;
  }
  .person-title {
    color: var(--muted);
    font-size: 15px;
    margin-top: 6px;
  }
  .divider {
    width: 2px; height: 64px;
    background: var(--red);
  }
  .contact-list { list-style: none; color: var(--white); font-size: 15px; line-height: 1.45; }
  .contact-list li { display: flex; align-items: center; gap: 7px; }
  .contact-list svg { width: 11px; height: 11px; fill: var(--red); flex: none; }
  .address {
    position: absolute;
    left: 0; right: 0; bottom: 70px;
    text-align: center;
    color: var(--white);
    font-size: 15px;
  }
</style>
</head>
<body>
  <section class="card card--brand">
    <span class="brand-dot"></span>
    <span class="brand-name">Brindovalle.com</span>
  </section>

  <section class="card card--contact">
    <div class="contact-top">
      <div class="person">
        <div class="person-name">Marco Dellari</div>
        <div class="person-title">Director</div>
      </div>
      <div class="divider"></div>
      <ul class="contact-list">
        <li>
          <svg viewBox="0 0 12 12" aria-hidden="true"><path d="M2.5 0.5l2 2.5-1 1.3c.7 1.6 2 2.9 3.6 3.6l1.3-1 2.5 2-1 2.1C5.2 11 1 6.8.4 1.6z"/></svg>
          555-014-2290
        </li>
        <li>
          <svg viewBox="0 0 12 12" aria-hidden="true"><path d="M0 2h12v8H0z M0 2l6 4.5L12 2" stroke="#1b1b1c" stroke-width="1"/></svg>
          info@brindovalle.com
        </li>
        <li>
          <svg viewBox="0 0 12 12" aria-hidden="true"><circle cx="6" cy="6" r="5.5"/></svg>
          brindovalle
        </li>
      </ul>
    </div>
    <p class="address">2240 W Linden, Ashford, Ohio 44012</p>
  </section>
</body>
</html>
```